Business Card Design Project

This is the first time we use our new logo. We need a business card that we can use both on our institutional corporate relationships and also that works for our staff that deals with consumers directly.

VELUNDA is a new company dedicated to empower consumers and to provide them with the best choices for specialized health care using the latest telemedicine technology (medicine at a distance via videoconference).

We want to print this cards in high quality materials and process. We will like designs that allow us to use UV spot varnish and other techniques that will differentiate us.

We are including Two different versions of Color logos. In addition we are including white over black background logos. Those can be used replacing the black for a color.

Please note this is the first time we will be creating any corporate materials with our new logo and colors.

Target Market(s)

34+ consumers of medium high and high socioeconomic levels.

Industry/Entity Type

Health

Requirements
Must have
• Our logo on its original colors
Should not have
• Any other graphical element or design that is not our logo

```html
<!DOCTYPE html>
<html lang="en">
<head>
<meta charset="utf-8">
<title>VELUNDA Business Card</title>
<link href="https://fonts.googleapis.com/css2?family=Mulish:wght@400;600;800&display=swap" rel="stylesheet">
<style>
  :root {
    --page-bg: #ecedf3;
    --card-white: #ffffff;
    --sky-blue: #56b3de;
    --brand-blue: #1f74b9;
    --navy: #18557f;
    --ink: #1d1d1f;
    --rule: #cfd3d8;
  }
  html, body {
    margin: 0;
    padding: 0;
    width: 1200px;
    height: 987px;
    overflow: hidden;
    background: var(--page-bg);
    font-family: "Mulish", Arial, sans-serif;
  }
  .sheet {
    position: relative;
    width: 1200px;
    height: 987px;
  }
  .card {
    position: absolute;
    left: 220px;
    width: 760px;
    height: 434px;
    border-radius: 34px;
    overflow: hidden;
    box-shadow: 0 6px 18px rgba(40, 50, 70, 0.18);
  }
  .card-front { top: 38px; background: var(--card-white); }
  .card-back { top: 512px; background: var(--brand-blue); }

  .front-shapes {
    position: absolute;
    inset: 0;
  }
  .brand-lockup {
    position: absolute;
    left: 44px;
    top: 160px;
    display: flex;
    align-items: center;
    gap: 12px;
  }
  .brand-dot {
    width: 26px;
    height: 26px;
    border-radius: 50%;
    background: var(--navy);
  }
  .brand-name {
    font-weight: 800;
    font-size: 50px;
    letter-spacing: 3px;
    color: var(--navy);
    line-height: 1;
  }
  .contact-list {
    position: absolute;
    left: 44px;
    top: 268px;
    margin: 0;
    padding: 0 22px 0 0;
    list-style: none;
    font-size: 17px;
    color: var(--ink);
    line-height: 26px;
    border-right: 2px solid var(--rule);
  }
  .contact-list li {
    display: flex;
    align-items: center;
    gap: 9px;
  }
  .contact-icon {
    width: 14px;
    height: 14px;
    flex: none;
  }
  .address {
    position: absolute;
    left: 270px;
    top: 290px;
    margin: 0;
    font-size: 18px;
    line-height: 26px;
    color: var(--ink);
    font-style: normal;
  }
  .person {
    position: absolute;
    right: 54px;
    top: 150px;
    text-align: right;
    color: var(--card-white);
  }
  .person-name {
    margin: 0;
    font-weight: 800;
    font-size: 36px;
    letter-spacing: 1px;
  }
  .person-title {
    margin: 4px 0 0;
    font-weight: 400;
    font-size: 26px;
  }

  .back-lockup {
    position: absolute;
    inset: 0;
    display: flex;
    flex-direction: column;
    align-items: center;
    justify-content: center;
    gap: 34px;
  }
  .back-brand {
    display: flex;
    align-items: center;
    gap: 18px;
  }
  .back-dot {
    width: 40px;
    height: 40px;
    border-radius: 50%;
    background: var(--card-white);
  }
  .back-name {
    font-weight: 800;
    font-size: 76px;
    letter-spacing: 4px;
    color: var(--card-white);
    line-height: 1;
  }
  .back-url {
    font-size: 22px;
    letter-spacing: 7px;
    color: var(--card-white);
  }
</style>
</head>
<body>
<main class="sheet">

  <section class="card card-front" aria-label="Card front">
    <svg class="front-shapes" width="760" height="434" viewBox="0 0 760 434">
      <path fill="var(--sky-blue)" d="M90 0 C330 0 470 170 560 300 C610 370 660 434 720 434 L760 434 L760 0 Z"/>
      <path fill="none" stroke="var(--navy)" stroke-width="11" d="M70 -4 C305 0 445 170 536 302 C585 372 630 434 690 440"/>
    </svg>

    <div class="brand-lockup">
      <span class="brand-dot"></span>
      <span class="brand-name">VELUNDA</span>
    </div>

    <ul class="contact-list">
      <li>
        <svg class="contact-icon" viewBox="0 0 14 14"><circle cx="7" cy="7" r="7" fill="var(--navy)"/><path d="M4.5 3.5 L6 3.5 L6.6 5.4 L5.6 6.2 Q6.4 7.8 7.9 8.5 L8.7 7.5 L10.5 8.1 L10.5 9.6 Q6.5 10 4.4 5.5 Z" fill="#fff"/></svg>
        012-555-0147
      </li>
      <li>
        <svg class="contact-icon" viewBox="0 0 14 14"><circle cx="7" cy="7" r="7" fill="var(--navy)"/><path d="M4.5 3.5 L6 3.5 L6.6 5.4 L5.6 6.2 Q6.4 7.8 7.9 8.5 L8.7 7.5 L10.5 8.1 L10.5 9.6 Q6.5 10 4.4 5.5 Z" fill="#fff"/></svg>
        012-555-0147
      </li>
      <li>
        <svg class="contact-icon" viewBox="0 0 14 14"><rect x="0.5" y="2.5" width="13" height="9" rx="1.5" fill="var(--navy)"/><path d="M1.5 3.5 L7 8 L12.5 3.5" fill="none" stroke="#fff" stroke-width="1.2"/></svg>
        name@velunda.com
      </li>
      <li>
        <svg class="contact-icon" viewBox="0 0 14 14"><circle cx="7" cy="7" r="6.2" fill="none" stroke="var(--navy)" stroke-width="1.4"/><ellipse cx="7" cy="7" rx="2.6" ry="6.2" fill="none" stroke="var(--navy)" stroke-width="1.1"/><path d="M1 7 H13 M2 4 H12 M2 10 H12" stroke="var(--navy)" stroke-width="1"/></svg>
        www.velunda.com
      </li>
    </ul>

    <address class="address">
      Street Name, City Name<br>
      State, City Zip Code
    </address>

    <div class="person">
      <p class="person-name">Your Name</p>
      <p class="person-title">Title</p>
    </div>
  </section>

  <section class="card card-back" aria-label="Card back">
    <div class="back-lockup">
      <div class="back-brand">
        <span class="back-dot"></span>
        <span class="back-name">VELUNDA</span>
      </div>
      <span class="back-url">www.velunda.com</span>
    </div>
  </section>

</main>
</body>
</html>
```